BOLD & MINIMALIST DESIGN NEEDED

We want a very bold but minimalistic business card design that is impactful and utilizes both sides of the business card. Our current logo is included for your use.

We want bold fonts and good use of negative space. We don't want the logo to overpower the design.

Target Market(s)

Professionals who are building new commercial buildings.

Industry/Entity Type

Construction

Contact Information for Business Card

Name, Title, email, office phone, cell phone, website

Font styles to use
Serif
Sans Serif

Requirements
Must have
• Bold design!

```html
<!DOCTYPE html>
<html lang="en">
<head>
<meta charset="utf-8">
<title>Ridgeline Design + Build — Business Card</title>
<link href="https://fonts.googleapis.com/css2?family=Montserrat:wght@400;500;700;800&display=swap" rel="stylesheet">
<style>
  :root {
    --stage: #3b3b3b;
    --paper: #ffffff;
    --ink: #1a1a1a;
    --muted: #555555;
    --green: #5a8a2a;
    --green-bright: #7ac142;
    --card-black: #161616;
  }
  * { box-sizing: border-box; margin: 0; padding: 0; }
  html, body {
    width: 1200px; height: 791px; overflow: hidden;
    background: var(--stage);
    font-family: "Montserrat", Arial, sans-serif;
  }
  .stage {
    width: 1200px; height: 791px;
    display: flex; align-items: center; justify-content: center; gap: 48px;
  }
  .card {
    position: relative;
    width: 540px; height: 309px;
    border-bottom: 4px solid var(--green);
    box-shadow: 0 14px 30px rgba(0,0,0,0.35);
    overflow: hidden;
  }
  /* Front */
  .card-front { background: var(--paper); }
  .holder {
    position: absolute; right: 34px; top: 34px; text-align: right;
  }
  .holder-name {
    color: var(--green); font-weight: 800; font-size: 22px; letter-spacing: 0.5px;
  }
  .holder-title {
    color: var(--muted); font-weight: 400; font-size: 13px; margin-top: 2px;
  }
  .divider-top {
    position: absolute; right: 34px; top: 96px; width: 300px; height: 1px;
    background: var(--green);
  }
  .brand {
    position: absolute; left: 34px; top: 132px;
    display: flex; align-items: center; gap: 10px;
  }
  .brand-mark { width: 16px; height: 16px; background: var(--green-bright); }
  .brand-name {
    color: var(--ink); font-weight: 800; font-size: 24px; letter-spacing: 1px;
  }
  .divider-bottom {
    position: absolute; left: 34px; top: 206px; width: 230px; height: 1px;
    background: var(--green);
  }
  .contact-list {
    position: absolute; left: 34px; top: 216px; list-style: none;
  }
  .contact-list li {
    display: flex; align-items: center; gap: 8px;
    font-size: 12.5px; color: var(--muted); line-height: 19px;
  }
  .contact-list svg { width: 11px; height: 11px; fill: var(--green); flex: none; }
  /* Back */
  .card-back { background: var(--card-black); }
  .back-pattern {
    position: absolute; inset: 0;
    background: linear-gradient(120deg, #0d0d0d 0%, #1e1e1e 55%, #3a3a3a 100%);
  }
  .back-brand {
    position: absolute; right: 70px; bottom: 80px;
    display: flex; align-items: center; gap: 10px;
  }
  .back-brand .brand-mark { background: var(--green-bright); }
  .back-brand .brand-name { color: var(--paper); font-size: 20px; }
</style>
</head>
<body>
<main class="stage">
  <section class="card card-front" aria-label="Business card front">
    <div class="holder">
      <p class="holder-name">MARCUS TRENT</p>
      <p class="holder-title">President</p>
    </div>
    <div class="divider-top"></div>

    <div class="brand">
      <span class="brand-mark"></span>
      <span class="brand-name">RIDGELINE</span>
    </div>

    <div class="divider-bottom"></div>
    <ul class="contact-list">
      <li>
        <svg viewBox="0 0 24 24"><path d="M6.6 10.8a15 15 0 0 0 6.6 6.6l2.2-2.2a1 1 0 0 1 1-.25 11.4 11.4 0 0 0 3.6.6 1 1 0 0 1 1 1V20a1 1 0 0 1-1 1A17 17 0 0 1 3 4a1 1 0 0 1 1-1h3.5a1 1 0 0 1 1 1c0 1.25.2 2.45.6 3.6a1 1 0 0 1-.25 1z"/></svg>
        555-014-2200
      </li>
      <li>
        <svg viewBox="0 0 24 24"><path d="M7 1h10a2 2 0 0 1 2 2v18a2 2 0 0 1-2 2H7a2 2 0 0 1-2-2V3a2 2 0 0 1 2-2zm0 3v14h10V4z"/></svg>
        555-014-2200
      </li>
      <li>
        <svg viewBox="0 0 24 24"><path d="M2 5h20v14H2zm2 2v.5l8 5 8-5V7l-8 5z"/></svg>
        m.trent@rdb-build.com
      </li>
      <li>
        <svg viewBox="0 0 24 24"><path d="M12 2a10 10 0 1 0 0 20 10 10 0 0 0 0-20zm6.9 9h-3a15 15 0 0 0-1.4-6A8 8 0 0 1 18.9 11zM12 4c.9 1.3 1.7 3.9 1.9 7h-3.8C10.3 7.9 11.1 5.3 12 4zM9.5 5a15 15 0 0 0-1.4 6h-3A8 8 0 0 1 9.5 5zm-4.4 8h3a15 15 0 0 0 1.4 6A8 8 0 0 1 5.1 13zM12 20c-.9-1.3-1.7-3.9-1.9-7h3.8c-.2 3.1-1 5.7-1.9 7zm2.5-1a15 15 0 0 0 1.4-6h3a8 8 0 0 1-4.4 6z"/></svg>
        www.rdb-build.com
      </li>
    </ul>
  </section>

  <section class="card card-back" aria-label="Business card back">
    <div class="back-pattern" role="img" aria-label="Repeating tonal brand-mark pattern in black and dark grey gloss"></div>
    <div class="back-brand">
      <span class="brand-mark"></span>
      <span class="brand-name">RIDGELINE</span>
    </div>
  </section>
</main>
</body>
</html>
```